Visitenkarten-Design für Garten- und Landschaftspflege
Nerapo Kulm setzte meine Vorstellungen absolut super um ich kann Ihn nur weiter empfehlen. vielen dank
Zielgruppe
Baumpflege, Baumfällung, Garten und Landschaftspflege meine zielgruppe sind Privatpersonen im alter von 20-100Jahren
Aufgabenstellung
Sehr geehrte Damen und Herren, die visitenkarte sollte die angaben so enthalten wie sie auf der von mir gestallteten Visitenkarten sind ( meine ist kein maß der Dinge). Ich habe mein Logo leider nur als 3.jpg Datei. Das Logo darf im Design erändert werden aber bitte nur Feinheiten ansonsten stehen ihnen alle türen offen um kreativ zu sein.
mit freundlichen Grüßen Jonas Vehmar

```html
<!DOCTYPE html>
<html lang="de">
<head>
<meta charset="utf-8">
<title>Baumpflege Vehmar – Visitenkarte</title>
<link rel="stylesheet" href="https://fonts.googleapis.com/css2?family=Fira+Sans:wght@400;500;600&display=swap">
<style>
  :root {
    --backdrop: #dcdcdc;
    --forest: #007a5c;
    --forest-deep: #0b6a4f;
    --meadow: #97c045;
    --meadow-light: #a6cb55;
    --ink: #0e3a3e;
    --paper: #ffffff;
    --shadow: rgba(0, 0, 0, 0.28);
  }
  * { box-sizing: border-box; margin: 0; padding: 0; }
  html, body {
    width: 1200px;
    height: 2437px;
    overflow: hidden;
    background: var(--backdrop);
    font-family: "Fira Sans", sans-serif;
  }
  .sheet { position: relative; width: 1200px; height: 2437px; }

  .card {
    position: absolute;
    left: 133px;
    width: 962px;
    height: 619px;
    background: var(--meadow);
    box-shadow: 22px 22px 26px var(--shadow);
    overflow: hidden;
  }
  .card--front { top: 119px; }
  .card--back  { top: 873px; height: 622px; outline: 1px solid #1d3a2c; }

  .sky-band {
    position: absolute;
    left: 0; top: 0;
    width: 100%;
    background: var(--forest);
  }
  .card--front .sky-band { height: 289px; }
  .card--back  .sky-band { height: 137px; }

  .scene-illustration {
    position: absolute;
    background: linear-gradient(180deg, var(--meadow-light) 0%, var(--meadow) 70%, var(--forest-deep) 100%);
  }
  .card--front .scene-illustration { left: 21px; top: 12px; width: 730px; height: 277px; }
  .card--back  .scene-illustration { left: 662px; top: 15px; width: 203px; height: 122px; }

  .brand-name {
    position: absolute;
    left: 0; right: 0;
    top: 318px;
    text-align: center;
    color: var(--paper);
    font-weight: 600;
    font-size: 90px;
    line-height: 1;
    letter-spacing: 0.5px;
  }
  .contact {
    position: absolute;
    left: 40px; right: 40px;
    top: 438px;
    font-size: 33px;
    line-height: 48px;
    color: var(--paper);
    text-align: center;
  }
  .contact .role-line { color: var(--ink); font-weight: 600; }
  .contact .dot { color: var(--forest); }
  .contact .role-line .dot { color: var(--ink); }

  .services-title {
    position: absolute;
    left: 66px;
    top: 80px;
    color: var(--paper);
    font-weight: 500;
    font-size: 56px;
    line-height: 1;
  }
  .services-list {
    position: absolute;
    left: 0;
    top: 204px;
    list-style: none;
    color: var(--paper);
    font-size: 35px;
    line-height: 52px;
  }
  .services-list li { position: relative; padding-left: 67px; }
  .services-list li::before {
    content: "";
    position: absolute;
    left: 0; top: 24px;
    width: 39px; height: 6px;
    background: var(--forest);
  }
</style>
</head>
<body>
<main class="sheet">

  <section class="card card--front">
    <div class="sky-band"></div>
    <div class="scene-illustration" role="img" aria-label="Illustration: großer Baum mit Schatten zwischen zwei Holzzäunen auf einer Wiese"></div>
    <h1 class="brand-name">Baumpflege Vehmar</h1>
    <div class="contact">
      <p class="role-line">Jonas Vehmar <span class="dot">•</span> Fachagrarwirt Baumpflege &amp; -sanierung</p>
      <p>Lindenweg 4 <span class="dot">•</span> 84321 Hollerbach <span class="dot">•</span> Tel. 0170 555 12 34</p>
      <p>kontakt@baumpflege-vehmar.de <span class="dot">•</span> baumpflege-vehmar.de</p>
    </div>
  </section>

  <section class="card card--back">
    <div class="sky-band"></div>
    <div class="scene-illustration" role="img" aria-label="Illustration: kleiner Baum mit Schatten am Horizont"></div>
    <h2 class="services-title">Unsere Leistungen</h2>
    <ul class="services-list">
      <li>Neu-Pflanzungen</li>
      <li>Herstellen der Verkehrssicherheit von Bäumen</li>
      <li>Kronenrückschnitt (Einkürzung und Kronenpflege)</li>
      <li>Prüfen von Bäumen auf Standsicherheit</li>
      <li>Fällen von Bäumen</li>
      <li>Fräsen von Wurzelstöcken</li>
      <li>Anbau und Fertigung von Gartenhäusern nach Maß</li>
    </ul>
  </section>

</main>
</body>
</html>
```